Website for Reiki and Wellness Courses

I teach online courses in Reiki and wellness/self-development and am needing a new website.

The focus of the website will be to provide descriptions of the courses as well as include a blog and pages where students in my courses will visit for additional information.

Note: courses are NOT hosted on this site.
The focus of this website will be to encourage viewers to enroll in courses as well as opt in to the email list.

I will upload copy soon. My old website is: http://brightfernstudies.example. Please do not use existing logo.

Target Market(s)

Alternative health, wellness, spirituality, personal development. Males and females of all ages seeking to improve their health and life.

Industry/Entity Type

Health And Wellness

Logo Text

No text (please do not use existing logo)

Coding

Coded - Design and coding required

Number of Pages Required

5+ page

Requirements
Must have
• 1. Home page
• 2. About page
• 3. Courses page that outlines courses (there are currently 6 courses with 1 coming soon)
• 4. Individual course page (maybe a template that I can adjust color and pictures for with each course)
• 5. Blog
• 6. Student Area that outlines all Student Areas
• 7. Individual Student Area page (maybe a template that I can adjust color and pictures for with each course)
• 8. Shop page (note: items will not currently be purchased through website - it will be a link to quillmarket for a book).
• 9. Student thank-you page (maybe a template that I can adjust color and pictures for with each course) this is the page students are directed to at end of course with vouchers for other courses.
• Opt-in for the home page, course pages, blog and thank-you pages
Nice to have
• I would like the design to be calm, clean and soothing. Ideally visitors feel relaxed when viewing the site and are encouraged to explore the courses, subscribe to the email list and purchase a product.
• ~ Testimonials page
• ~ Contact page
• I tend to gravitate towards blues, greys and purples as well as monochromatic color schemes.
Should not have
• Contact form on home page
• phone number on home page
• location/physical address
• dates for blog posts

```html
<!DOCTYPE html>
<html lang="en">
<head>
<meta charset="utf-8">
<title>Bright Fern Studies</title>
<link rel="stylesheet" href="https://fonts.googleapis.com/css2?family=Roboto+Slab:wght@300;400;700&family=Lato:ital,wght@0,400;0,700;1,400&family=Lora:ital@1&display=swap">
<style>
:root{
  --ink:#222;
  --muted:#555;
  --accent-red:#d9322a;
  --royal:#27439b;
  --purple:#6554a9;
  --purple-field:#8274bf;
  --card-title:#5a3f9c;
  --grey-band:#efefef;
  --line:#d8d8d8;
  --btn-red:#c9262b;
  --btn-orange:#f39229;
  --btn-green:#2a9e4a;
  --footer:#1d2319;
  --footer-bar:#141812;
  --footer-accent:#5fb23a;
  --footer-rule:#3a4035;
  --white:#fff;
}
*{box-sizing:border-box;margin:0;padding:0}
html,body{width:1200px;height:2597px;overflow:hidden}
body{position:relative;background:var(--white);font-family:'Lato',sans-serif;color:var(--ink)}
.abs{position:absolute}
.slab{font-family:'Roboto Slab',serif}

/* header */
.site-header{position:absolute;left:0;top:0;width:1200px;height:128px;background:var(--white)}
.brand{position:absolute;left:99px;top:38px;font-family:'Roboto Slab',serif;font-size:34px;font-weight:400;color:var(--ink);display:flex;align-items:center;gap:12px}
.brand-dot{width:18px;height:18px;border-radius:50%;background:var(--purple)}
.contact-strip{position:absolute;right:98px;top:22px;display:flex;align-items:center;gap:8px;font-size:15px}
.main-nav{position:absolute;right:98px;top:84px;display:flex;font-family:'Roboto Slab',serif;font-size:17px}
.main-nav a{color:var(--ink);text-decoration:none;padding:0 14px;border-left:1px solid #ccc;line-height:24px}
.main-nav a:first-child{border-left:none;color:var(--accent-red)}
.main-nav a:last-child{padding-right:0}

/* hero */
.hero{position:absolute;left:0;top:128px;width:1200px;height:473px;background:linear-gradient(135deg,#5a4636 0%,#8a6a52 35%,#b8a496 60%,#d9cfc8 100%)}
.hero-caption{position:absolute;left:0;bottom:0;width:100%;height:64px;background:rgba(30,30,30,.75);color:var(--white);font-family:'Roboto Slab',serif;font-size:33px;text-align:center;line-height:64px}

/* opt-in */
.optin{position:absolute;left:0;top:601px;width:1200px;height:260px;background:var(--purple);color:var(--white);text-align:center}
.optin h2{position:absolute;top:18px;width:100%;font-family:'Roboto Slab',serif;font-weight:400;font-size:26px}
.optin p{position:absolute;top:88px;left:160px;width:880px;font-size:13.5px;line-height:20px}
.field{position:absolute;top:147px;width:205px;height:35px;background:var(--purple-field);color:#eee;font-size:12.5px;text-align:left;padding:10px 11px}
.btn-outline{position:absolute;border:1.5px solid var(--white);border-radius:9px;font-family:'Roboto Slab',serif;font-size:16px;text-align:center}

.section-title{position:absolute;width:100%;text-align:center;font-family:'Roboto Slab',serif;font-weight:400;font-size:36px;color:var(--ink)}
.section-title em{font-style:normal;color:var(--royal)}
.divider{position:absolute;left:99px;width:1002px;height:1px;background:var(--line)}
.divider-mark{position:absolute;left:592px;width:16px;height:16px;border-radius:50%;background:var(--purple)}

/* courses */
.course{position:absolute;top:1006px;width:230px;text-align:center}
.course h3{font-family:'Lora',serif;font-style:italic;font-weight:400;font-size:19px;line-height:27px;color:var(--card-title);height:58px}
.course .thumb{margin:6px auto 0;width:214px;height:181px;border:6px solid var(--white);box-shadow:0 0 0 1px #ccc,0 2px 5px rgba(0,0,0,.25)}
.course p{margin:30px auto 0;width:200px;font-size:13px;line-height:19px;color:var(--muted)}
.course a{display:block;margin-top:6px;font-size:13px;font-weight:700;color:var(--card-title);text-decoration:underline}

/* welcome */
.welcome{position:absolute;left:0;top:1394px;width:1200px;height:428px;background:var(--grey-band)}
.welcome p{position:absolute;left:135px;top:158px;width:930px;text-align:center;font-size:13.5px;line-height:23.5px;color:#444}
.btn-red-outline{position:absolute;left:542px;top:260px;width:114px;height:36px;border:1.5px solid var(--accent-red);border-radius:8px;background:var(--white);color:var(--accent-red);font-family:'Roboto Slab',serif;font-size:16px;text-align:center;line-height:33px}
.feature{position:absolute;top:315px;width:240px;height:61px;border-radius:3px;color:var(--white);font-family:'Roboto Slab',serif;font-size:16px;line-height:19px;display:flex;align-items:center;gap:14px;padding-left:14px}
.feature .icon{width:36px;height:36px;border-radius:50%;border:2px solid rgba(255,255,255,.8)}

/* reviews */
.review{position:absolute;top:1980px;width:460px}
.avatar{position:absolute;left:0;top:0;width:104px;height:98px;border-radius:50%;border:5px solid #666;background:linear-gradient(160deg,#d9c1ad,#8e6f5c)}
.review .name{position:absolute;left:125px;top:30px;font-weight:700;font-size:15px}
.review .role{position:absolute;left:125px;top:52px;font-size:13.5px;color:#555}
.review blockquote{position:absolute;left:0;top:130px;width:455px;font-style:italic;font-size:14px;line-height:25.5px;color:#333;text-indent:28px}
.quote-mark{position:absolute;left:0;top:134px}

/* footer */
.site-footer{position:absolute;left:0;top:2269px;width:1200px;height:328px;background:var(--footer);color:#ddd}
.footer-heading{position:absolute;top:43px;font-family:'Lato',sans-serif;font-weight:400;font-size:18px;color:var(--white)}
.footer-heading em{font-style:normal;color:var(--footer-accent)}
.links{position:absolute;left:111px;top:92px;list-style:none;font-size:12.5px;line-height:29px}
.links li::before{content:"•";color:var(--footer-accent);margin-right:8px}
.footer-rule{position:absolute;top:40px;width:1px;height:220px;background:var(--footer-rule)}
.footer-bar{position:absolute;left:0;bottom:0;width:100%;height:42px;background:var(--footer-bar);font-size:12px;color:#ccc}
.card{display:inline-block;width:36px;height:22px;border-radius:3px;margin-left:6px;vertical-align:middle}
</style>
</head>
<body>

<header class="site-header">
  <div class="brand"><span class="brand-dot"></span>Bright Fern Studies</div>
  <div class="contact-strip">
    <svg width="16" height="12" viewBox="0 0 16 12"><rect width="16" height="12" fill="#d9322a"/><path d="M0 0 L8 7 L16 0" stroke="#fff" stroke-width="1.5" fill="none"/></svg>
    <span>info@brightfernstudies.example</span>
  </div>
  <nav class="main-nav">
    <a>Home</a><a>About Us</a><a>Online Courses</a><a>Student Areas</a><a>Testimonials</a><a>Contact Us</a>
  </nav>
</header>

<section class="hero" role="img" aria-label="Photo of a person typing on a laptop with a coffee mug, screen reading Reiki Training Online">
  <div class="hero-caption">Online Courses In Reiki And Wellness &amp; Self-development</div>
</section>

<section class="optin">
  <h2>Stay Inspired</h2>
  <div class="abs" style="left:520px;top:70px;width:160px;height:1px;background:rgba(255,255,255,.35)"></div>
  <div class="abs" style="left:592px;top:62px;width:16px;height:16px;border-radius:50%;background:#f2a33a"></div>
  <p>Receive information and articles each month to keep you feeling inspired. As a thank-you, you will also receive access to soothing music you can download for use in your Reiki sessions and meditation.</p>
  <div class="field" style="left:268px">First Name</div>
  <div class="field" style="left:500px">Last Name</div>
  <div class="field" style="left:731px">Email Address</div>
  <div class="btn-outline" style="left:521px;top:199px;width:158px;height:37px;line-height:34px">Yes-Count Me In</div>
</section>

<section class="courses">
  <h2 class="section-title" style="top:896px"><em>Our</em> Bright Fern Studies</h2>
  <div class="divider" style="top:963px"></div>
  <div class="divider-mark" style="top:948px"></div>

  <article class="course" style="left:98px">
    <h3>Reiki Level I, II &amp;<br>Master Certification</h3>
    <div class="thumb" role="img" aria-label="Stacked stones on a beach at sunrise" style="background:linear-gradient(180deg,#7fa6c9 0%,#c7b7a0 55%,#8e7a63 100%);box-shadow:0 0 0 2px #6554a9"></div>
    <p>Learn about Reiki, a universal energy that has been used successfully all over....</p>
    <a>Read More</a>
  </article>
  <article class="course" style="left:356px">
    <h3>Animal Reiki<br>Practitioner Certification</h3>
    <div class="thumb" role="img" aria-label="Small white dog between two open hands" style="background:linear-gradient(180deg,#6e9ed8,#dfe4ea 55%,#5f8fcc)"></div>
    <p>In this course you will learn how to use Animal Reiki; a simple, non-invasive..</p>
    <a>Read More</a>
  </article>
  <article class="course" style="left:612px">
    <h3>Acupressure and Reiki for<br>Anxiety and Depression</h3>
    <div class="thumb" role="img" aria-label="Green leaf resting in raked sand" style="background:linear-gradient(160deg,#dcd6cb,#b9b1a3)"></div>
    <p>Do you feel down more often than up? Or do you find fear is preventing you...</p>
    <a>Read More</a>
  </article>
  <article class="course" style="left:870px">
    <h3>Your Soul is Calling<br>Creating Your Ideal Life</h3>
    <div class="thumb" role="img" aria-label="Soft pink abstract swirl" style="background:radial-gradient(circle at 50% 45%,#f4dfe9,#c77aa4 60%,#9a4d7c)"></div>
    <p>What would it be like to live the life you were meant to live? To have the world around you in...</p>
    <a>Read More</a>
  </article>
</section>

<section class="welcome">
  <h2 class="section-title" style="top:40px"><em>Welcome to</em> Bright Fern Studies</h2>
  <div class="abs" style="left:592px;top:98px;width:16px;height:16px;border-radius:50%;background:var(--purple)"></div>
  <p>Thought to be centuries old and rediscovered in the late 1800's, Reiki (pronounced ray-key) is a healing and enlightenment system. reikihealing Reiki can be translated into "Universal (Rei) Life Energy (Ki)". As a practitioner of Reiki, you attune your awareness to this energy and utilize it for the physical and emotional healing of self and others. Reiki is non-denominational and can be practiced by everyone, regardless of their religious and spiritual beliefs. Reiki can be performed hands-on in person or from a distance.</p>
  <div class="btn-red-outline">Read More</div>
  <div class="feature" style="left:185px;background:var(--btn-red)"><span class="icon"></span>How<br>Reiki Works</div>
  <div class="feature" style="left:481px;background:var(--btn-orange)"><span class="icon"></span>Traditional Usui Reiki<br>Master Certification</div>
  <div class="feature" style="left:776px;background:var(--btn-green);font-size:17px"><span class="icon"></span>Our<br>Resources</div>
</section>

<section class="reviews">
  <h2 class="section-title" style="top:1862px"><em>Happy Customer</em> Reviews</h2>
  <div class="divider" style="top:1926px"></div>
  <div class="divider-mark" style="top:1911px"></div>
  <svg class="abs" style="left:68px;top:2064px" width="18" height="30" viewBox="0 0 18 30"><path d="M15 2 L3 15 L15 28" stroke="#bbb" stroke-width="4" fill="none"/></svg>
  <svg class="abs" style="left:1114px;top:2064px" width="18" height="30" viewBox="0 0 18 30"><path d="M3 2 L15 15 L3 28" stroke="#bbb" stroke-width="4" fill="none"/></svg>
  <div class="abs" style="left:599px;top:1980px;width:1px;height:250px;background:#e2e2e2"></div>

  <article class="review" style="left:111px">
    <div class="avatar" role="img" aria-label="Portrait of a reviewer"></div>
    <div class="name">Mrs. Lena Marsh</div>
    <div class="role">Business Wooman</div>
    <svg class="quote-mark" width="22" height="14" viewBox="0 0 22 14"><path d="M0 14V7Q0 0 8 0V3Q4 3 4 7H8V14ZM12 14V7Q12 0 20 0V3Q16 3 16 7H20V14Z" fill="#bbb"/></svg>
    <blockquote>Utm tellus dolor, dapibus eget, elemen velmki cursus eleifelita arnean auctorbni wisi et urnam. Lorem ipsum dolor sit amet, conse ctetur adipiscing elit. Nulla in sollicitudin velit, bibendum velit.Cras vel facilisis ipsum, et venenatis risus.</blockquote>
  </article>
  <article class="review" style="left:639px">
    <div class="avatar" role="img" aria-label="Portrait of a reviewer"></div>
    <div class="name">Mrs. Lena Marsh</div>
    <div class="role">Business Wooman</div>
    <svg class="quote-mark" width="22" height="14" viewBox="0 0 22 14"><path d="M0 14V7Q0 0 8 0V3Q4 3 4 7H8V14ZM12 14V7Q12 0 20 0V3Q16 3 16 7H20V14Z" fill="#bbb"/></svg>
    <blockquote>Utm tellus dolor, dapibus eget, elemen velmki cursus eleifelita arnean auctorbni wisi et urnam. Lorem ipsum dolor sit amet, conse ctetur adipiscing elit. Nulla in sollicitudin velit, bibendum velit.Cras vel facilisis ipsum, et venenatis risus.</blockquote>
  </article>
</section>

<footer class="site-footer">
  <h4 class="footer-heading" style="left:111px">Quick <em>Links</em></h4>
  <ul class="links"><li>Home</li><li>About</li><li>Courses</li><li>Student Areas</li><li>Blog</li><li>Contact</li></ul>
  <div class="footer-rule" style="left:272px"></div>

  <h4 class="footer-heading" style="left:317px">Contact <em>Details</em></h4>
  <svg class="abs" style="left:318px;top:103px" width="14" height="10" viewBox="0 0 14 10"><rect width="14" height="10" fill="#5fb23a"/><path d="M0 0 L7 6 L14 0" stroke="#1d2319" fill="none"/></svg>
  <div class="abs" style="left:346px;top:100px;font-size:12.5px">info@brightfernstudies.example</div>

  <div class="footer-rule" style="left:888px"></div>
  <div class="abs slab" style="left:905px;top:115px;width:200px;text-align:center;font-size:24px;color:#8d918a">Bright Fern Studies</div>

  <div class="footer-bar">
    <div class="abs" style="left:100px;top:14px">Copyright © 2016 Bright Fern Studies. All Rights Reserved.</div>
    <div class="abs" style="right:102px;top:10px">We Accept
      <span class="card" style="background:#3c6fb5"></span><span class="card" style="background:#e8e8e8"></span><span class="card" style="background:#f5f5f5"></span><span class="card" style="background:#4a9bd8"></span><span class="card" style="background:#e9a33a"></span>
    </div>
  </div>
</footer>

</body>
</html>
```